Dalvick's Business Card

I need some designs for a new business card including the new logo attached. An old example of our business card is also attached to show all the data that should be included on the new design.
**I added some more examples someone had mocked up**

Contact Information for Business Card

Should include all info on other examples uploaded.

```html
<!DOCTYPE html>
<html lang="en">
<head>
<meta charset="utf-8">
<title>Dalvick's Business Card</title>
<link href="https://fonts.googleapis.com/css2?family=Montserrat:wght@400;600;700&family=Oswald:wght@600&display=swap" rel="stylesheet">
<style>
  :root {
    --backdrop: #3a3a3a;
    --brand-blue: #0a74c4;
    --brand-blue-deep: #0566b3;
    --brand-red: #e31e26;
    --paper: #f7f7f7;
    --ink-light: #ffffff;
  }
  html, body {
    margin: 0;
    padding: 0;
    width: 1200px;
    height: 1200px;
    overflow: hidden;
    background: var(--backdrop);
  }
  .canvas {
    width: 1200px;
    height: 1200px;
    display: flex;
    flex-direction: column;
    align-items: center;
    justify-content: center;
    gap: 60px;
  }
  .card {
    position: relative;
    width: 880px;
    height: 503px;
    border-radius: 34px;
    overflow: hidden;
    background: linear-gradient(135deg, var(--brand-blue) 0%, var(--brand-blue-deep) 100%);
    box-shadow: 0 18px 40px rgba(0,0,0,0.45);
    font-family: "Montserrat", sans-serif;
    color: var(--ink-light);
  }
  /* Contact side */
  .brand-panel {
    position: absolute;
    left: 0;
    top: 0;
    width: 420px;
    height: 503px;
  }
  .brand-panel-mark {
    position: absolute;
    left: 70px;
    top: 215px;
    display: flex;
    align-items: center;
    gap: 14px;
    font-weight: 700;
    font-size: 44px;
    color: var(--brand-blue);
  }
  .mark-dot {
    width: 22px;
    height: 22px;
    border-radius: 50%;
    background: var(--brand-red);
  }
  .contact-block {
    position: absolute;
    left: 470px;
    top: 96px;
  }
  .person-name {
    margin: 0 0 24px;
    font-weight: 700;
    font-size: 38px;
    letter-spacing: 0.5px;
  }
  .contact-list {
    list-style: none;
    margin: 0;
    padding: 0;
  }
  .contact-item {
    display: flex;
    align-items: center;
    gap: 12px;
    font-size: 21px;
    font-weight: 400;
    margin-bottom: 8px;
  }
  .contact-icon {
    width: 22px;
    height: 22px;
    flex: none;
  }
  .credentials {
    margin: 40px 0 0;
    font-family: "Oswald", sans-serif;
    font-weight: 600;
    font-size: 27px;
    line-height: 1.15;
    text-transform: uppercase;
  }
  /* Brand side */
  .brand-front {
    display: flex;
    align-items: center;
    justify-content: center;
  }
  .brand-name {
    display: flex;
    align-items: center;
    gap: 22px;
    font-weight: 700;
    font-size: 104px;
    letter-spacing: 2px;
    text-transform: uppercase;
  }
  .brand-name .mark-dot {
    width: 44px;
    height: 44px;
  }
</style>
</head>
<body>
<main class="canvas">

  <section class="card card-contact">
    <svg class="brand-panel" viewBox="0 0 420 503" aria-hidden="true">
      <path d="M0 0 H180 C330 60 440 250 360 400 C320 470 250 503 200 503 H0 Z" fill="#f7f7f7"/>
    </svg>
    <div class="brand-panel-mark"><span class="mark-dot"></span>Dalvick's</div>

    <div class="contact-block">
      <h1 class="person-name">REID DALVICK</h1>
      <ul class="contact-list">
        <li class="contact-item">
          <svg class="contact-icon" viewBox="0 0 24 24"><path d="M6.6 10.8a15 15 0 0 0 6.6 6.6l2.2-2.2a1 1 0 0 1 1-.25 11.4 11.4 0 0 0 3.6.57 1 1 0 0 1 1 1V20a1 1 0 0 1-1 1A17 17 0 0 1 3 4a1 1 0 0 1 1-1h3.5a1 1 0 0 1 1 1c0 1.25.2 2.45.57 3.57a1 1 0 0 1-.25 1z" fill="#fff"/></svg>
          555.014.2290
        </li>
        <li class="contact-item">
          <svg class="contact-icon" viewBox="0 0 24 24"><rect x="2" y="5" width="20" height="14" fill="#fff"/><path d="M2 5 L12 13 L22 5" fill="none" stroke="#0a74c4" stroke-width="2"/></svg>
          hvacdalvick@mailbox.com
        </li>
        <li class="contact-item">
          <svg class="contact-icon" viewBox="0 0 24 24" fill="none" stroke="#fff" stroke-width="1.6"><circle cx="12" cy="12" r="10"/><ellipse cx="12" cy="12" rx="4.5" ry="10"/><path d="M2 12h20M4 7h16M4 17h16"/></svg>
          www.yourwebsite.com
        </li>
      </ul>
      <p class="credentials">Licensed &amp; Insured<br>Family Owned &amp; Operated</p>
    </div>
  </section>

  <section class="card brand-front">
    <div class="brand-name"><span class="mark-dot"></span>Dalvick's</div>
  </section>

</main>
</body>
</html>
```